Business Card Design

We like to use greens as you will see in our logo (but not TOO much green). We are a Dental Clinic in a somewhat eccentric community. We do not like the dated sharp designs which we see many dentists use. We're looking for something bright and fresh while still maintaining the integrity of the profession. Elegance is not necessarily what we are going for... we need for the design to be "mature" but also up-lifting.

See our logo.
Updates

Project Deadline Extended
Reason: We have 5 designs which we like. But we'd like to see a few more before committing to a design.

Project Deadline Extended
Reason: We are awaiting revisions to this project. We are still welcoming designs while we wait to see if designers are able to provide to us the revisions we require in order to proceed with a selection.

Target Market(s)

Younger families - ages late 20's to early 40's

Industry/Entity Type

Business

Contact Information for Business Card

Corwel T. Banfry DDS 2730 W. Halvert Rd. Ste. 7 Royal Oak, MI 48391 (248)555-0174 FX (248)555-0189 info@BrightwellDentalCareMi.com BrigthwellDentalCareMi.com on the back of the card we need an appointment reminder (For____ Date___ Time____) with "If you are unable to keep your appointment, kindly give 48 hours notice" at the bottom. No use of teeth in the design. DOUBLE SIDED DESIGN

Requirements
Should not have
• The use of pictures of teeth

```html
<!DOCTYPE html>
<html lang="en">
<head>
<meta charset="utf-8">
<title>Brightwell Dental Care – Business Card</title>
<link rel="stylesheet" href="https://fonts.googleapis.com/css2?family=Cinzel:wght@500&family=Open+Sans:ital,wght@0,400;0,600;0,700;1,400&display=swap">
<style>
  :root {
    --green-dark: #1a6b35;
    --green-mid: #2f8a3e;
    --green-light: #7dc142;
    --ink: #2b2b2b;
    --rule: #9a9a9a;
    --card: #ffffff;
    --backdrop: #eceeea;
    --box-line: #3a3a3a;
  }
  * { box-sizing: border-box; margin: 0; padding: 0; }
  html, body {
    width: 1200px; height: 1179px; overflow: hidden;
    background: var(--backdrop);
    font-family: "Open Sans", Arial, sans-serif;
    color: var(--ink);
  }
  .canvas { position: relative; width: 1200px; height: 1179px; }
  .card {
    position: absolute; width: 918px; height: 524px;
    background: var(--card);
    box-shadow: 0 2px 8px rgba(0,0,0,0.18);
    overflow: hidden;
  }
  .card--front { left: 262px; top: 34px; }
  .card--back { left: 27px; top: 604px; }

  .brand {
    position: absolute; display: flex; align-items: center; gap: 14px;
    color: var(--green-dark); font-weight: 600; line-height: 1.05;
  }
  .brand__dot { flex: none; border-radius: 50%; background: var(--green-light); }
  .brand--front { left: 0; right: 0; top: 110px; justify-content: center; font-size: 54px; }
  .brand--front .brand__dot { width: 44px; height: 44px; }
  .brand--back { left: 70px; top: 40px; font-size: 34px; }
  .brand--back .brand__dot { width: 28px; height: 28px; }
  .brand__name span { display: block; }

  .identity { position: absolute; right: 514px; top: 318px; text-align: right; font-size: 20px; line-height: 1.5; }
  .identity__name { color: var(--green-dark); font-weight: 700; font-size: 29px; line-height: 1.2; }
  .identity__title { margin: 6px 0 10px; }
  .divider { position: absolute; left: 422px; top: 322px; width: 1px; height: 148px; background: var(--rule); }
  .contacts { position: absolute; left: 438px; top: 318px; list-style: none; font-size: 20px; }
  .contacts li { display: flex; align-items: center; gap: 8px; height: 40px; }
  .contacts svg { width: 18px; height: 18px; fill: var(--ink); flex: none; }
  .front-band { position: absolute; left: 0; bottom: 0; width: 918px; height: 24px; }

  .appt-title {
    position: absolute; left: 79px; top: 170px;
    font-family: "Cinzel", Georgia, serif; font-size: 32px; color: var(--green-dark); letter-spacing: 1px;
  }
  .field { position: absolute; left: 79px; font-size: 23px; display: flex; align-items: baseline; gap: 10px; }
  .field__line { display: inline-block; border-bottom: 2px dotted #555; height: 1px; }
  .field--name { top: 244px; }
  .field--date { top: 308px; }
  .field--next { top: 375px; }
  .slot { position: absolute; width: 165px; height: 36px; border: 2px solid var(--box-line); border-radius: 5px; }
  .notice { position: absolute; left: 79px; right: 20px; top: 450px; font-style: italic; font-size: 23px; }
  .days { position: absolute; right: 26px; top: 0; }
  .day { position: absolute; right: 0; display: flex; align-items: center; gap: 14px; font-weight: 600; font-size: 23px; }
  .day__box { width: 57px; height: 34px; border: 2px solid var(--box-line); border-radius: 4px; }
  .back-band { position: absolute; left: 0; bottom: 0; width: 100%; height: 12px; background: var(--green-dark); }
</style>
</head>
<body>
<div class="canvas">

  <section class="card card--front">
    <div class="brand brand--front">
      <span class="brand__dot"></span>
      <span class="brand__name">Brightwell Dental Care</span>
    </div>

    <div class="identity">
      <div class="identity__name">Corwel T. Banfry</div>
      <div class="identity__title">DDS</div>
      <div>2730 W. Halvert Rd.</div>
      <div>Ste. 7 Royal Oak, MI 48391</div>
    </div>

    <div class="divider"></div>

    <ul class="contacts">
      <li><svg viewBox="0 0 20 20"><circle cx="10" cy="10" r="9" fill="none" stroke="#2b2b2b" stroke-width="1.6"/><path d="M7 5l2 2-1 1.5c.6 1.4 1.6 2.4 3 3l1.5-1 2 2-1.2 1.5C9.8 14 6 10.2 5.5 6.2z"/></svg>(248)555-0174</li>
      <li><svg viewBox="0 0 20 20"><rect x="2" y="8" width="16" height="9" rx="1.5"/><rect x="5" y="3" width="10" height="6" fill="none" stroke="#2b2b2b" stroke-width="1.6"/><rect x="5" y="11" width="10" height="2" fill="#fff"/></svg>(248)555-0189</li>
      <li><svg viewBox="0 0 20 20"><rect x="2" y="4" width="16" height="12" rx="1.5"/><path d="M3 5l7 6 7-6" fill="none" stroke="#fff" stroke-width="1.6"/></svg>info@BrightwellDentalCareMi.com</li>
      <li><svg viewBox="0 0 20 20"><g fill="none" stroke="#2b2b2b" stroke-width="1.5"><circle cx="10" cy="10" r="8"/><ellipse cx="10" cy="10" rx="3.5" ry="8"/><path d="M2 10h16M3.5 6h13M3.5 14h13"/></g></svg>BrigthwellDentalCareMi.com</li>
    </ul>

    <svg class="front-band" viewBox="0 0 918 24" preserveAspectRatio="none" aria-hidden="true">
      <polygon points="0,0 420,0 396,24 0,24" fill="var(--green-dark)"/>
      <polygon points="432,0 918,0 918,24 408,24" fill="var(--green-light)"/>
    </svg>
  </section>

  <section class="card card--back">
    <div class="brand brand--back">
      <span class="brand__dot"></span>
      <span class="brand__name"><span>Brightwell</span><span>Dental Care</span></span>
    </div>

    <h2 class="appt-title">YOUR APPOINTMENT</h2>

    <div class="field field--name">Name :<span class="field__line" style="width:505px"></span></div>
    <div class="field field--date">Date :<span class="field__line" style="width:168px"></span>Time :<span class="field__line" style="width:158px"></span>am / pm</div>
    <div class="field field--next">Next Appointment</div>
    <div class="slot" style="left:326px; top:373px"></div>
    <div class="slot" style="left:529px; top:373px"></div>

    <p class="notice">If you are unable to keep your appointment, kindly give 48 hours notice</p>

    <div class="days">
      <div class="day" style="top:78px">MON<span class="day__box"></span></div>
      <div class="day" style="top:142px">TUE<span class="day__box"></span></div>
      <div class="day" style="top:204px">WED<span class="day__box"></span></div>
      <div class="day" style="top:268px">THU<span class="day__box"></span></div>
      <div class="day" style="top:326px">FRI<span class="day__box"></span></div>
      <div class="day" style="top:381px">SAT<span class="day__box"></span></div>
    </div>

    <div class="back-band"></div>
  </section>

</div>
</body>
</html>
```